strength and conditioning business focused on helping people move more efficiently

I need a business card designed for a Philadelphia based company called Brsk Lft Motion (pronounced Brisk Lift). We offer fitness professional services with the idea of helping people feel better and move optimally. We do this by designing and walking through individualized programs as well as minor soft tissue work. Our perfect client would be athletes but we will be marketing to parents who have children that are active They remember their former athletic days and want to get as close as possible back to that feeling. Attached will be the official logo and logo formats. I would love for the design to communicate trustworthy and creative. I would also love for the design to be square with rounded edges.

Target Market(s)

Parents of athletic children
former athletes
athletes

Industry/Entity Type

Fitness

Contact Information for Business Card

Business: Brsk Lft Performance
Name: Coach Calvin Ashworth
Position: Strength and Conditioning Coach / Certified Personal Trainer
Contact: coach.ash@brsklft.com
Text: (555)204-7781

Font styles to use
Serif
Sans Serif

Colors
fbee38
fbee3e
0255a3
3176b5
ffffff

Requirements
Must have
• use of logo
Nice to have
• Square design
rounded edges

```html
<!DOCTYPE html>
<html lang="en">
<head>
<meta charset="utf-8">
<title>Brsk Lft Motion – Business Card</title>
<link rel="stylesheet" href="https://fonts.googleapis.com/css2?family=Arimo:wght@400;700&display=swap">
<style>
  :root {
    --stage: #0b3282;
    --navy: #0a3587;
    --navy-card: #0b3a8e;
    --gold: #fcc800;
    --white: #ffffff;
    --ink: #222222;
    --rule: #b9b9b9;
  }
  * { margin: 0; padding: 0; box-sizing: border-box; }
  html, body { width: 1200px; height: 859px; overflow: hidden; }
  body {
    background: var(--stage);
    font-family: "Arimo", Arial, sans-serif;
    position: relative;
  }
  .card {
    position: absolute;
    top: 208px;
    width: 446px;
    height: 446px;
    border-radius: 32px;
    overflow: hidden;
  }
  .card--front { left: 142px; background: var(--white); }
  .card--back  { left: 626px; background: var(--navy-card); }

  .brand {
    position: absolute;
    left: 0; right: 0;
    display: flex;
    align-items: center;
    justify-content: center;
    gap: 14px;
  }
  .card--front .brand { top: 88px; }
  .card--back .brand  { top: 185px; }
  .brand__mark {
    width: 46px; height: 46px;
    border-radius: 50%;
    flex: none;
  }
  .card--front .brand__mark { background: var(--gold); }
  .card--back .brand__mark  { background: var(--gold); }
  .brand__name {
    font-weight: 700;
    font-size: 44px;
    letter-spacing: 0.5px;
    line-height: 1;
  }
  .card--front .brand__name { color: var(--navy); }
  .card--back .brand__name  { color: var(--white); }

  .person {
    position: absolute;
    top: 210px; left: 0; right: 0;
    text-align: center;
  }
  .person__name {
    font-weight: 700;
    font-size: 21px;
    color: var(--navy);
  }
  .person__name .first { color: var(--gold); }
  .person__role {
    margin-top: 5px;
    font-size: 15px;
    line-height: 21px;
    color: var(--ink);
  }

  .divider {
    position: absolute;
    top: 293px; left: 0; right: 0;
    display: flex;
    align-items: center;
    justify-content: center;
    gap: 4px;
  }
  .divider__rule { width: 44px; height: 1px; background: var(--rule); margin: 0 6px; }
  .divider svg { display: block; }

  .contact {
    position: absolute;
    top: 328px; left: 0; right: 0;
    text-align: center;
    font-size: 17px;
    line-height: 21.5px;
    color: var(--ink);
  }

  .footer-band {
    position: absolute;
    left: 0; right: 0; bottom: 0;
    height: 27px;
    background: var(--navy);
    border-top: 6px solid var(--gold);
  }
</style>
</head>
<body>

<section class="card card--front">
  <div class="brand">
    <span class="brand__mark"></span>
    <span class="brand__name">Brsk Lft Motion</span>
  </div>

  <div class="person">
    <p class="person__name"><span class="first">Coach Calvin</span> Ashworth</p>
    <p class="person__role">Strength and Conditioning Coach /<br>Certified Personal Trainer</p>
  </div>

  <div class="divider">
    <span class="divider__rule"></span>
    <svg width="24" height="24" viewBox="0 0 24 24" aria-label="Phone">
      <circle cx="12" cy="12" r="12" fill="var(--navy)"/>
      <path d="M8.2 6.5l2 .2 1 2.6-1.3 1c.6 1.4 1.6 2.4 3 3l1-1.3 2.6 1 .2 2c-.2.8-1 1.3-1.8 1.2-4.2-.5-7.3-3.6-7.8-7.8-.1-.8.4-1.6 1.1-1.9z" fill="var(--white)"/>
    </svg>
    <svg width="24" height="24" viewBox="0 0 24 24" aria-label="Email">
      <circle cx="12" cy="12" r="12" fill="var(--navy)"/>
      <rect x="6.5" y="8" width="11" height="8" rx="1" fill="var(--white)"/>
      <path d="M6.8 8.4l5.2 4.2 5.2-4.2" fill="none" stroke="var(--navy)" stroke-width="1.2"/>
    </svg>
    <svg width="24" height="24" viewBox="0 0 24 24" aria-label="Website">
      <circle cx="12" cy="12" r="12" fill="var(--navy)"/>
      <circle cx="12" cy="12" r="6" fill="none" stroke="var(--white)" stroke-width="1.3"/>
      <ellipse cx="12" cy="12" rx="2.6" ry="6" fill="none" stroke="var(--white)" stroke-width="1.1"/>
      <path d="M6 12h12" stroke="var(--white)" stroke-width="1.1"/>
    </svg>
    <span class="divider__rule"></span>
  </div>

  <div class="contact">
    <p>(555)204-7781</p>
    <p>coach.ash@brsklft.com</p>
    <p>www.brsklft.com</p>
  </div>

  <div class="footer-band"></div>
</section>

<section class="card card--back">
  <div class="brand">
    <span class="brand__mark"></span>
    <span class="brand__name">Brsk Lft Motion</span>
  </div>
</section>

</body>
</html>
```